Web Developer Needs a Business Card Design

I need a personal business card design that represents me as a web developer for potential employers. I would like the background to be a dark color on the front for contrast with my logo and name. The back will have all my information along with a smaller version of the logo. I want something with a modern look and feel, not too conservative. This will be used for potential employers and freelance work.

Industry/Entity Type

Business

Contact Information for Business Card

Front should have my logo and name. The back should have all my personal information which would include: name: Tom Varulek, phone: 570-614-3098, email: tomvarulek@quillbox.net, website url: www.tomvarulek.net, logo, web developer.

Font styles to use
Sans Serif

Requirements
Must have
• Must include my logo. The color palette base color will be the logo color.

```html
<!DOCTYPE html>
<html lang="en">
<head>
<meta charset="utf-8">
<title>Tom Varulek — Business Card</title>
<link rel="stylesheet" href="https://fonts.googleapis.com/css2?family=Roboto:wght@400;500&display=swap">
<style>
  :root {
    --backdrop: #a3a0a0;
    --card: #0c0c0c;
    --card-soft: #161616;
    --mint: #5ce1c0;
    --mint-faint: rgba(92, 225, 192, 0.16);
    --silver-faint: rgba(201, 201, 201, 0.08);
  }
  * { margin: 0; padding: 0; box-sizing: border-box; }
  html, body { width: 1200px; height: 1200px; overflow: hidden; }
  body {
    position: relative;
    background: var(--backdrop);
    font-family: "Roboto", Arial, sans-serif;
  }
  .card {
    position: absolute;
    width: 712px;
    height: 420px;
    border-radius: 22px;
    overflow: hidden;
    background: var(--card);
  }
  .card-front { left: 238px; top: 117px; }
  .card-back  { left: 234px; top: 643px; }

  .desk-backdrop {
    position: absolute;
    inset: 0;
    background: radial-gradient(circle at 50% 55%, var(--card) 30%, var(--card-soft) 100%);
  }

  .edge-accent {
    position: absolute;
    left: 0; top: 0;
    width: 140px; height: 420px;
    background: linear-gradient(90deg, var(--mint-faint) 0%, var(--silver-faint) 55%, transparent 100%);
  }

  .brand-mark {
    position: absolute;
    display: flex;
    align-items: center;
    gap: 14px;
    color: var(--mint);
    font-weight: 500;
    white-space: nowrap;
    transform: translate(-50%, -50%);
  }
  .brand-mark .dot {
    width: 22px; height: 22px;
    border-radius: 50%;
    background: var(--mint);
  }
  .card-front .brand-mark { left: 50%; top: 50%; font-size: 44px; }
  .card-back .brand-mark  { left: 538px; top: 207px; font-size: 36px; }

  .identity {
    position: absolute;
    right: 346px;
    top: 118px;
    text-align: right;
    color: var(--mint);
  }
  .identity .name { font-size: 31px; font-weight: 400; letter-spacing: 0.3px; }
  .identity .role { font-size: 17px; margin-top: 8px; }

  .contact-list {
    position: absolute;
    right: 383px;
    top: 214px;
    list-style: none;
    color: var(--mint);
    font-size: 19px;
    text-align: right;
    white-space: nowrap;
  }
  .contact-list li {
    height: 28px;
    line-height: 28px;
    position: relative;
  }
  .contact-list .icon {
    position: absolute;
    right: -36px;
    top: 6px;
    width: 16px; height: 16px;
  }
</style>
</head>
<body>

  <section class="card card-front" aria-label="Card front">
    <div class="desk-backdrop" role="img" aria-label="Faint dark desk scene with keyboard and tablet"></div>
    <div class="brand-mark"><span class="dot"></span>Tom Varulek</div>
  </section>

  <section class="card card-back" aria-label="Card back">
    <div class="desk-backdrop" role="img" aria-label="Faint dark desk scene with keyboard and tablet"></div>
    <div class="edge-accent" role="img" aria-label="Mint and silver line decoration along the left edge"></div>

    <div class="identity">
      <div class="name">Tom Varulek</div>
      <div class="role">Web Developer</div>
    </div>

    <ul class="contact-list">
      <li>570-614-3098
        <svg class="icon" viewBox="0 0 16 16" aria-hidden="true"><path fill="var(--mint)" d="M1 5c0-2 3-3 7-3s7 1 7 3v1h-4V4.5H5V6H1zM4 7h8l2 7H2z"/></svg>
      </li>
      <li>tomvarulek@quillbox.net
        <svg class="icon" viewBox="0 0 16 16" aria-hidden="true"><rect x="1" y="3" width="14" height="10" fill="var(--mint)"/><polyline points="1,3 8,9 15,3" fill="none" stroke="var(--card)" stroke-width="1.4"/></svg>
      </li>
      <li>www.tomvarulek.net
        <svg class="icon" viewBox="0 0 16 16" aria-hidden="true"><circle cx="8" cy="8" r="7" fill="var(--mint)"/><g fill="none" stroke="var(--card)" stroke-width="1"><ellipse cx="8" cy="8" rx="3" ry="7"/><line x1="1" y1="8" x2="15" y2="8"/></g></svg>
      </li>
    </ul>

    <div class="brand-mark"><span class="dot"></span>Varulek</div>
  </section>

</body>
</html>
```